Online homewares store needs a web design

We need a web design for a new high-end online homewares store. We are starting small with only 5 major categories.

Rugs
Bathe
Dine
Decorative
Sleep

This is just for design. No coding needed.

Please make high-end, sophisticated and minimal.

I have included some pictures to give you an idea of the products. I would like to showcase some of the pictures on the web page.

The website will be using an e-commerce function.

I have included the logo studio nine harbors.

I like this website
http://mapleandquarrylane.example/

or

borvanest.example.au

Simple but effective - not too busy

Project Deadline Extended
Reason: I would like to extend my deadline to give designers more time to do quality work - as requested!! Thanks.

Target Market(s)

Females in the age bracket of 25-45

Males who are very house proud 25-45

Industry/Entity Type

Store

Requirements
Must have
• Upmarket

```html
<!DOCTYPE html>
<html lang="en">
<head>
<meta charset="utf-8">
<title>studio nine harbors — Home</title>
<link rel="stylesheet" href="https://fonts.googleapis.com/css2?family=Quicksand:wght@300&family=Source+Sans+3:wght@400;600&family=Arimo:wght@400&display=swap">
<style>
  :root {
    --ink: #000000;
    --pink: #ff2d78;
    --white: #ffffff;
    --text-grey: #555555;
    --footer: #2b2b2b;
    --rule: #c9c9c9;
    --caption: rgba(70, 70, 70, 0.72);
  }
  * { box-sizing: border-box; margin: 0; padding: 0; }
  html, body { width: 916px; height: 1200px; overflow: hidden; background: var(--white); }
  body { position: relative; font-family: "Source Sans 3", Arial, sans-serif; color: var(--white); }

  .site-header { position: absolute; left: 0; top: 0; width: 916px; height: 139px; background: var(--ink); }
  .account-links { position: absolute; top: 30px; left: 565px; font-size: 12px; display: flex; gap: 7px; }
  .cart { position: absolute; top: 30px; left: 760px; font-size: 12px; display: flex; align-items: center; gap: 6px; }
  .brand { position: absolute; left: 62px; top: 52px; font-family: "Quicksand", sans-serif; font-weight: 300; font-size: 40px; letter-spacing: -0.5px; color: var(--white); }
  .main-nav { position: absolute; top: 80px; left: 523px; display: flex; font-size: 13px; letter-spacing: -0.2px; }
  .main-nav a { color: var(--white); text-decoration: none; height: 28px; line-height: 28px; padding: 0 12px; margin-right: 5px; }
  .main-nav a.is-active { background: var(--pink); }

  .hero { position: absolute; left: 0; top: 139px; width: 916px; height: 429px;
    background: linear-gradient(115deg, #6e5544 0%, #c9b7a8 22%, #e6d9d2 38%, #c75a7c 55%, #6f8fbf 68%, #d47a92 80%, #8b6f64 100%); }
  .hero-arrow { position: absolute; top: 329px; width: 46px; height: 46px; }
  .hero-arrow.prev { left: 65px; }
  .hero-arrow.next { left: 802px; }

  .intro-band { position: absolute; left: 0; top: 568px; width: 916px; height: 114px; background: var(--pink); }
  .intro-title { position: absolute; left: 90px; top: 30px; font-size: 24px; font-weight: 600; letter-spacing: 0.3px; }
  .intro-rule { position: absolute; left: 338px; top: 23px; width: 1px; height: 44px; background: rgba(255,255,255,0.55); }
  .intro-text { position: absolute; left: 365px; top: 26px; width: 480px; font-size: 12px; line-height: 19px; }

  .category-panel { position: absolute; left: 69px; top: 658px; width: 782px; height: 340px; background: var(--white);
    box-shadow: 0 8px 16px rgba(0,0,0,0.08); border-radius: 3px; }
  .category-tile { position: absolute; width: 243px; height: 140px; border-radius: 2px; overflow: hidden; }
  .category-photo { position: absolute; inset: 0; }
  .category-caption { position: absolute; left: 0; bottom: 0; width: 100%; height: 37px; background: var(--caption);
    display: flex; align-items: center; justify-content: space-between; padding: 0 12px 0 14px; font-size: 15px; letter-spacing: -0.2px; }

  .contact-strip { position: absolute; left: 0; top: 1025px; width: 916px; height: 45px; font-family: "Arimo", Arial, sans-serif; color: var(--text-grey); }
  .contact-item { position: absolute; display: flex; align-items: center; gap: 14px; }
  .contact-rule { position: absolute; top: 6px; width: 1px; height: 36px; background: var(--rule); }
  .contact-main { font-size: 12.5px; }
  .contact-sub { font-size: 10.5px; margin-top: 6px; }

  .site-footer { position: absolute; left: 0; top: 1093px; width: 916px; height: 107px; background: var(--footer); font-family: "Arimo", Arial, sans-serif; }
  .footer-links { position: absolute; left: 63px; top: 35px; font-size: 11px; display: flex; gap: 6px; }
  .copyright { position: absolute; left: 63px; top: 63px; font-size: 11px; }
  .social-list { position: absolute; left: 671px; top: 36px; display: flex; gap: 11px; }
  .social-list span { width: 36px; height: 36px; border: 1.5px solid #cfcfcf; border-radius: 50%; }
</style>
</head>
<body>
  <header class="site-header">
    <nav class="account-links"><span>Register</span><span>|</span><span>Login</span><span>|</span><span>My Account</span></nav>
    <div class="cart">
      <svg width="15" height="13" viewBox="0 0 15 13" aria-hidden="true"><path d="M1 1h2l2 7h7l2-5H4" fill="none" stroke="#fff" stroke-width="1.3"/><circle cx="6" cy="11" r="1.2" fill="#fff"/><circle cx="11" cy="11" r="1.2" fill="#fff"/></svg>
      <span>Cart (0) items</span>
    </div>
    <div class="brand">studio nine harbors</div>
    <nav class="main-nav">
      <a class="is-active" href="#">HOME</a><a href="#">ABOUT US</a><a href="#">PRODUCTS</a><a href="#">CONTACT US</a>
    </nav>
  </header>

  <section class="hero" role="img" aria-label="Close-up of a colourful woven pom-pom blanket with fringed edge"></section>
  <svg class="hero-arrow prev" viewBox="0 0 46 46" aria-hidden="true"><circle cx="23" cy="23" r="23" fill="rgba(30,30,30,0.55)"/><path d="M26 15l-8 8 8 8" fill="none" stroke="#fff" stroke-width="1.5"/></svg>
  <svg class="hero-arrow next" viewBox="0 0 46 46" aria-hidden="true"><circle cx="23" cy="23" r="23" fill="rgba(30,30,30,0.55)"/><path d="M20 15l8 8-8 8" fill="none" stroke="#fff" stroke-width="1.5"/></svg>

  <section class="intro-band">
    <h1 class="intro-title">MIRUM EST NOTARE</h1>
    <div class="intro-rule"></div>
    <p class="intro-text">Jerta baditaut onsequser untur magni dolores eoquie voluptate msequi nesciunt volup tatem accusantium dolorem consectetuer adipiscing elit aenean.</p>
  </section>

  <section class="category-panel" aria-label="Categories"></section>

  <a class="category-tile" style="left:78px;top:669px">
    <div class="category-photo" role="img" aria-label="Bare feet on a multicoloured felt ball rug" style="background:linear-gradient(135deg,#d9506a,#e9c06a 40%,#6cb0c8 70%,#9b5a8a)"></div>
    <div class="category-caption"><span>RUGS</span><svg width="20" height="20" viewBox="0 0 20 20"><circle cx="10" cy="10" r="9" fill="none" stroke="#fff" stroke-width="1.3"/><path d="M8.5 6l4 4-4 4" fill="none" stroke="#fff" stroke-width="1.3"/></svg></div>
  </a>
  <a class="category-tile" style="left:338px;top:669px">
    <div class="category-photo" role="img" aria-label="Folded woven bath towel with fringe and a bar of soap" style="background:linear-gradient(135deg,#8a8a8a,#c06a7c 40%,#e9e2da 60%,#7e8fb0)"></div>
    <div class="category-caption"><span>BATHE</span><svg width="20" height="20" viewBox="0 0 20 20"><circle cx="10" cy="10" r="9" fill="none" stroke="#fff" stroke-width="1.3"/><path d="M8.5 6l4 4-4 4" fill="none" stroke="#fff" stroke-width="1.3"/></svg></div>
  </a>
  <a class="category-tile" style="left:597px;top:669px">
    <div class="category-photo" role="img" aria-label="Wooden puzzle cheese boards with bread, cheese and herbs" style="background:linear-gradient(135deg,#d8cfc4,#c99a62 45%,#a8763f 80%,#6f7a3c)"></div>
    <div class="category-caption"><span>DINE</span><svg width="20" height="20" viewBox="0 0 20 20"><circle cx="10" cy="10" r="9" fill="none" stroke="#fff" stroke-width="1.3"/><path d="M8.5 6l4 4-4 4" fill="none" stroke="#fff" stroke-width="1.3"/></svg></div>
  </a>
  <a class="category-tile" style="left:78px;top:843px">
    <div class="category-photo" role="img" aria-label="Strands of colourful felt beads hanging beside a white ornament" style="background:linear-gradient(135deg,#e8e8e6,#d7d5d2 50%,#c9c3c0)"></div>
    <div class="category-caption"><span>DECORATIVE</span><svg width="20" height="20" viewBox="0 0 20 20"><circle cx="10" cy="10" r="9" fill="none" stroke="#fff" stroke-width="1.3"/><path d="M8.5 6l4 4-4 4" fill="none" stroke="#fff" stroke-width="1.3"/></svg></div>
  </a>
  <a class="category-tile" style="left:338px;top:843px">
    <div class="category-photo" role="img" aria-label="Bed with green patterned quilt and a bedside lamp" style="background:linear-gradient(135deg,#b8b3ae,#4f8a7c 45%,#2f6e63 75%,#a6355f)"></div>
    <div class="category-caption"><span>SLEEP</span><svg width="20" height="20" viewBox="0 0 20 20"><circle cx="10" cy="10" r="9" fill="none" stroke="#fff" stroke-width="1.3"/><path d="M8.5 6l4 4-4 4" fill="none" stroke="#fff" stroke-width="1.3"/></svg></div>
  </a>
  <a class="category-tile" style="left:597px;top:843px">
    <div class="category-photo" role="img" aria-label="Stacked patchwork floor cushions" style="background:linear-gradient(135deg,#f2f2f2,#c98a5a 35%,#b5533f 60%,#d9b46a)"></div>
    <div class="category-caption"><span>CUSHION</span><svg width="20" height="20" viewBox="0 0 20 20"><circle cx="10" cy="10" r="9" fill="none" stroke="#fff" stroke-width="1.3"/><path d="M8.5 6l4 4-4 4" fill="none" stroke="#fff" stroke-width="1.3"/></svg></div>
  </a>

  <section class="contact-strip">
    <div class="contact-item" style="left:69px;top:4px">
      <svg width="22" height="28" viewBox="0 0 22 28" aria-hidden="true"><path d="M11 1a9 9 0 0 0-9 9c0 7 9 17 9 17s9-10 9-17a9 9 0 0 0-9-9z" fill="#555"/><circle cx="11" cy="10" r="3.5" fill="#fff"/></svg>
      <div><div class="contact-main">Duis autem vel eum iriureHendrerit.</div><div class="contact-sub">Typi non habent claritatem insitam</div></div>
    </div>
    <div class="contact-rule" style="left:345px"></div>
    <div class="contact-item" style="left:408px;top:8px">
      <svg width="22" height="24" viewBox="0 0 22 24" aria-hidden="true"><path d="M5 1l4 5-2.5 3c1.5 3.5 4 6 7.5 7.5l3-2.5 4 4-3 4C10 21 1 12 1 4z" fill="#555"/></svg>
      <span class="contact-main">123 - 456 - 789</span>
    </div>
    <div class="contact-rule" style="left:586px"></div>
    <div class="contact-item" style="left:655px;top:10px">
      <svg width="35" height="22" viewBox="0 0 35 22" aria-hidden="true"><rect x="0" y="0" width="35" height="22" fill="#555"/><path d="M1 1l16.5 12L34 1M1 21l12-10M34 21L22 11" fill="none" stroke="#fff" stroke-width="1.4"/></svg>
      <span class="contact-main">hello@studionineharbors.example</span>
    </div>
  </section>

  <footer class="site-footer">
    <nav class="footer-links"><span>Home</span><span>|</span><span>About Us</span><span>|</span><span>Products</span><span>|</span><span>Contact Us</span></nav>
    <p class="copyright">Copyright © 2013. All Rights Reserved.</p>
    <div class="social-list" aria-label="Social links"><span></span><span></span><span></span><span></span></div>
  </footer>
</body>
</html>
```